Need a powerful, eye-catching book cover design for a Public Relations book for Lawyers.

We need a beautiful, elegant, and professional cover for a public relations book. We’ll be selling this both to (1) creative, experienced legal marketers, and (2) conservative lawyers. It must grab their attention visually, and have a bold, easy to read headline. The cover image may wrap around to the back cover.SIZE: 6 x 9” 100 pagesTITLE: The Ultimate Public Relations Handbook for LawyersSUBHEAD: Make millions using media and the InternetCO-AUTHORSRoss Fishman, JDJohn HellermanInclude a CALLOUT quote: “The definitive PR book. Simple and powerful.” – Hal Brevik, SkaddenGRAPHICS:You may use one of the attached photos, crop or flip them however you’d like, or use something else entirely. DESCRIPTION for the back cover:Why do some law firms have the best reputations or command the highest hourly rates? Why are some the go-to firms or thought leaders in particular specialties? Why are your competitors in the media more than you? Two words: Public relations. The co-authors are known worldwide as leaders in public relations, legal marketing, and branding. Neil Caskowitz is called, “A PR Guru.” Bench Notes magazine wrote ““Many people consider Dale Wrenbury to be the nation’s foremost expert on law firm marketing.”Hal Brevik built Marlowe into the first firm to generate $1 billion in revenue. Teresa Vandome is the nation’s go-to lawyer for women’s issues. Your home town’s top PI lawyer gets the first look at the biggest cases. Why? Strategic, intentional, effective PR. Are you tired of toiling in anonymity? Want to earn the attention of reporters and editors who can build your credentials and reputation for expertise? Wouldn’t it be nice to have more clients begging you to represent them because they heard you were the best in town? That is what public relations is designed to do. Want to get more respect, earn more clients, and charge higher rates? Get known as a thought leader in a specialty practice or industry? Public relations could be your most-important marketing tool. And this book will teach you precisely how. Ready to catapult your practice to new heights? Take a deep breath and dive in….

Target Market(s)

1. Creative marketing professionals
2. Conservative 40-year-old lawyers

Industry/Entity Type

Legal

Font styles to use
Serif

Requirements
Must have
• Want a simple, bold, eye catching design conveying professionalism and quality. This is a practical, how-to book. We need a simple design and strong headline that will work well at a small thumbnail size on Pagewell.
Nice to have
• Perhaps the microphone could wrap around the cover? A tight crop of a microphone that creates an abstract could work. Let's create something memorable.

```html
<!DOCTYPE html>
<html lang="en">
<head>
<meta charset="utf-8">
<title>The Complete Press Outreach Manual for Attorneys — Cover</title>
<link rel="stylesheet" href="https://fonts.googleapis.com/css2?family=Bebas+Neue&family=Roboto+Condensed:ital,wght@0,700;1,500&family=Roboto:wght@700&display=swap">
<style>
  :root {
    --page: #ffffff;
    --cover: #000000;
    --ink: #ffffff;
    --accent: #1a8fe8;
    --floor-light: #5e5e60;
    --floor-dark: #1a1a1b;
  }
  * { margin: 0; padding: 0; box-sizing: border-box; }
  html, body {
    width: 1036px; height: 1200px; overflow: hidden;
    background: var(--page);
  }
  .cover {
    position: absolute; left: 138px; top: 30px;
    width: 760px; height: 1140px;
    background: var(--cover);
    overflow: hidden;
  }
  .cover-photo {
    position: absolute; left: 0; top: 500px;
    width: 760px; height: 510px;
    background:
      radial-gradient(ellipse 70% 45% at 55% 35%, #2a2a2c 0%, transparent 70%),
      linear-gradient(180deg, var(--cover) 0%, #0b0b0c 45%, var(--floor-dark) 62%, var(--floor-light) 100%);
  }
  .title {
    position: absolute; left: 80px; top: 200px;
    font-family: "Bebas Neue", "Oswald", sans-serif;
    font-size: 88px; line-height: 0.9; color: var(--ink);
    letter-spacing: 0.5px;
  }
  .title .accent { color: var(--accent); }
  .subhead {
    position: absolute; left: 70px; top: 430px;
    padding: 4px 14px 6px;
    border: 1.5px solid var(--accent);
    font-family: "Roboto Condensed", "Arial Narrow", sans-serif;
    font-weight: 700; font-size: 34px; color: var(--ink);
    white-space: nowrap;
  }
  .subhead .accent { color: var(--accent); }
  .callout {
    position: absolute; right: 80px; top: 790px;
    text-align: right;
    font-family: "Roboto Condensed", "Arial Narrow", sans-serif;
    font-style: italic; font-weight: 500;
    font-size: 30px; line-height: 1.15; color: var(--ink);
  }
  .callout cite { display: block; color: var(--accent); font-style: italic; }
  .authors {
    position: absolute; left: 0; right: 0; top: 1010px; height: 130px;
    background: var(--cover);
    display: flex; align-items: center; justify-content: center;
    font-family: "Roboto", "Verdana", sans-serif; font-weight: 700;
    font-size: 27px; letter-spacing: 2px; word-spacing: 6px;
    color: var(--accent);
  }
</style>
</head>
<body>
  <main class="cover">
    <div class="cover-photo" role="img" aria-label="Tight close-up photograph of a black microphone head lying on a grey surface, lit from above"></div>

    <h1 class="title">
      The Complete<br>
      <span class="accent">Press Outreach</span><br>
      <span class="accent">Manual</span> for Attorneys
    </h1>

    <p class="subhead">Make Millions using <span class="accent">Media and the Internet</span></p>

    <blockquote class="callout">
      “The definitive PR book. Simple and powerful.”
      <cite>Hal Brevik, Marlowe</cite>
    </blockquote>

    <p class="authors">Dale Wrenbury &amp; JDNeil Caskowitz</p>
  </main>
</body>
</html>
```